KCA Waltz of our luminaries

My nonprofit social service agency is having a fun gala based on the TV show waltz of the luminaries, and we need the key design for an invitation. The event is a dinner and will have 7 local well-known people dance in a contest-like setting with a nationally known host. This does not need to be the final invitation (RSVP, list of dancers/hosts, etc.). All I need at this point is a great design for the cover to give this event an identity and entice people to attend and/or donate to the cause! Though our logo colors are blue/green/burgandy, this can use black/gold/silver/white as well. Our website is www.kcaohvalley.org if that helps explain who we are.

Also, it can be abstract. And it does not have to include ballroom dancers if the word mark or other graphics are eye catching.

Target Market(s)

Donors, upscale, higher income,45-70, men and women (though women will more likely make the decision to attend)

Industry/Entity Type

Tv

Requirements
Must have
• The wording to be incorporated into the invitation cover is:
Kindred Care Alliance
Celebrates Rising Strong Through Years with
Waltz of the Luminaries
hosted by Host Name (will give the final name when confirmed)

Saturday, November 8, 2014
7 pm
Marlowe Cincinnati Tidewater Court
Nice to have
• I'd like to see something other than ballroom dancers just to give my committee some options. Is it possible to show footprints of dancers (man's shoe with woman's high heels) as the design element? Something that can be used across the invite (rsvp card).
Should not have
• You have free range to create and have fun! If you use our logo colors, either choose one color as the focus, or just be sure to focus on green and burgandy together

```html
<!DOCTYPE html>
<html lang="en">
<head>
<meta charset="utf-8">
<title>Kindred Care Alliance – Waltz of the Luminaries</title>
<link rel="stylesheet" href="https://fonts.googleapis.com/css2?family=Montserrat:ital,wght@0,600;0,700;1,700&family=Great+Vibes&family=Libre+Baskerville&display=swap">
<style>
  :root {
    --ink: #000000;
    --panel-dark: #1a1a1a;
    --panel-light: #3a3a3a;
    --white: #ffffff;
    --gold-light: #fbe9a0;
    --gold-mid: #d9a928;
    --gold-deep: #9c6f0c;
  }
  html, body {
    margin: 0;
    padding: 0;
    width: 927px;
    height: 1200px;
    overflow: hidden;
    background: var(--ink);
  }
  .invitation-cover {
    display: block;
    width: 927px;
    height: 1200px;
  }
  .org-name {
    font-family: "Montserrat", sans-serif;
    font-weight: 700;
    fill: var(--gold-mid);
  }
  .tagline {
    font-family: "Montserrat", sans-serif;
    font-weight: 700;
    fill: var(--white);
  }
  .tagline-italic { font-style: italic; }
  .script {
    font-family: "Great Vibes", cursive;
  }
  .script-white { fill: var(--white); }
  .serif-link {
    font-family: "Libre Baskerville", serif;
    fill: var(--white);
  }
  .event-detail {
    font-family: "Montserrat", sans-serif;
    font-weight: 600;
    fill: var(--white);
  }
</style>
</head>
<body>
<svg class="invitation-cover" viewBox="0 0 927 1200" xmlns="http://www.w3.org/2000/svg">
  <defs>
    <linearGradient id="gold-fill" x1="0" y1="0" x2="0" y2="1">
      <stop offset="0" stop-color="var(--gold-light)"/>
      <stop offset="0.45" stop-color="var(--gold-mid)"/>
      <stop offset="0.6" stop-color="var(--gold-light)"/>
      <stop offset="1" stop-color="var(--gold-deep)"/>
    </linearGradient>
    <linearGradient id="gold-rule" x1="0" y1="0" x2="1" y2="0">
      <stop offset="0" stop-color="var(--gold-deep)"/>
      <stop offset="0.5" stop-color="var(--gold-light)"/>
      <stop offset="1" stop-color="var(--gold-deep)"/>
    </linearGradient>
    <radialGradient id="panel-glow" cx="0.5" cy="0.5" r="0.7">
      <stop offset="0" stop-color="var(--panel-light)"/>
      <stop offset="1" stop-color="var(--panel-dark)"/>
    </radialGradient>
  </defs>

  <!-- backdrop panel -->
  <g class="backdrop-panel" role="img" aria-label="Backdrop of soft grey spotlight circles in a grid">
    <rect x="66" y="60" width="796" height="786" rx="16" fill="url(#panel-glow)"/>
  </g>

  <!-- central medallion -->
  <circle class="medallion" cx="464" cy="456" r="356" fill="var(--ink)"/>

  <!-- organisation name -->
  <g class="org-mark">
    <circle cx="372" cy="150" r="16" fill="var(--gold-mid)"/>
    <text class="org-name" x="398" y="144" font-size="21">Kindred Care</text>
    <text class="org-name" x="398" y="170" font-size="21">Alliance</text>
  </g>

  <!-- tagline -->
  <text class="tagline tagline-italic" x="340" y="262" font-size="30" text-anchor="middle" textLength="268" lengthAdjust="spacingAndGlyphs">CELEBRATES</text>
  <text class="tagline" x="316" y="304" font-size="42" text-anchor="middle" textLength="346" lengthAdjust="spacingAndGlyphs">RISING STRONG</text>
  <text class="script script-white" x="186" y="350" font-size="50">through</text>
  <text class="tagline" x="336" y="350" font-size="42" textLength="160" lengthAdjust="spacingAndGlyphs">YEARS</text>
  <text class="script script-white" x="496" y="362" font-size="44">with</text>
  <path class="star" fill="url(#gold-fill)" d="M612 322 l7 15 16 2 -12 11 3 16 -14 -8 -14 8 3 -16 -12 -11 16 -2z"/>

  <!-- title word mark -->
  <text class="script" x="150" y="540" font-size="210" fill="url(#gold-fill)" stroke="var(--gold-deep)" stroke-width="1">Waltz</text>
  <text class="serif-link" x="590" y="575" font-size="52">of the</text>
  <text class="script" x="464" y="700" font-size="150" text-anchor="middle" textLength="640" lengthAdjust="spacingAndGlyphs" fill="url(#gold-fill)" stroke="var(--gold-deep)" stroke-width="1">Luminaries</text>

  <!-- event details -->
  <text class="event-detail" x="463" y="898" font-size="48" text-anchor="middle" textLength="780" lengthAdjust="spacingAndGlyphs">SATURDAY NOVEMBER 8<tspan font-size="28" dy="-18">TH</tspan></text>
  <rect class="rule" x="64" y="992" width="258" height="5" fill="url(#gold-rule)"/>
  <rect class="rule" x="604" y="992" width="258" height="5" fill="url(#gold-rule)"/>
  <text class="event-detail" x="463" y="1012" font-size="46" text-anchor="middle">7:00PM</text>
  <text class="event-detail" x="463" y="1086" font-size="38" text-anchor="middle" textLength="790" lengthAdjust="spacingAndGlyphs">MARLOWE CINCINNATI TIDEWATER COURT</text>
  <text class="event-detail" x="463" y="1152" font-size="46" text-anchor="middle" textLength="800" lengthAdjust="spacingAndGlyphs">HOSTED BY: XXXXXX XXXXXXX</text>
</svg>
</body>
</html>
```